Luxury Business Card Design for High-End Window Treatments

Gilded Slatworks
Custom Plantation Shutters & Architectural Shading Systems

⸻

BACK

Daniel Trevick
Owner

Custom Interior & Exterior Window Treatments

919-555-0148
gildedslatworks.com

I have included a picture that I’m hoping we can use on the back, but I’m also wondering if you can get rid of the ladder? Should we get rid of shutters , shades and blinds underneath Gilded Slatworks?

Target Market(s)

High-end residential homeowners, custom home builders, architects, interior designers, and luxury renovation clients seeking premium plantation shutters and motorized architectural shading systems.

Industry/Entity Type

Custom Window treatments

Contact Information for Business Card

Front Gilded Slatworks Custom Plantation Shutters Motorized Architectural Shading Systems BACK Daniel Trevick Owner 919-555-0148 GildedSlatworks.com Custom Interior & Exterior Window Treatments By Appointment

Requirements
Nice to have
• Not 100% sure on nice to halves or the color but you can definitely check out my website to get a better understanding of what I’m trying to do

```html
<!DOCTYPE html>
<html lang="en">
<head>
<meta charset="utf-8">
<title>Gilded Slatworks – Business Card</title>
<link href="https://fonts.googleapis.com/css2?family=Alegreya:wght@500&family=Montserrat:wght@300;400&family=Playfair+Display:wght@600&display=swap" rel="stylesheet">
<style>
  :root {
    --page: #e8e8eb;
    --ink-black: #000000;
    --cream: #efe8da;
    --white: #ffffff;
    --gold-name: #b39c5a;
    --gold-card: #a58f5e;
    --olive-stripe: #8f8a48;
    --tag-yellow: #ecc94c;
    --tag-yellow-bright: #f3d15e;
    --photo-light: #7f97b0;
    --photo-dark: #4b5052;
  }
  * { margin: 0; padding: 0; box-sizing: border-box; }
  html, body {
    width: 1200px; height: 1108px; overflow: hidden;
    background: var(--page);
  }
  .card {
    position: absolute;
    overflow: hidden;
  }
  .card--front {
    left: 219px; top: 50px; width: 774px; height: 473px;
    background: var(--ink-black);
  }
  .card--back {
    left: 217px; top: 568px; width: 776px; height: 457px;
    background: var(--gold-card);
  }
  .front-art {
    position: absolute; inset: 0;
  }
  .brand {
    position: absolute;
    text-align: center;
  }
  .brand__name {
    font-family: "Montserrat", sans-serif;
    font-weight: 300;
    color: var(--cream);
  }
  .brand__tagline {
    font-family: "Alegreya", serif;
    font-weight: 500;
    word-spacing: 0.45em;
  }
  .card--front .brand { left: 40px; top: 52px; width: 210px; }
  .card--front .brand__name { font-size: 38px; line-height: 47px; }
  .card--front .brand__tagline { font-size: 17px; line-height: 22px; color: var(--tag-yellow); margin-top: 2px; }

  .contact {
    position: absolute; left: 40px; top: 210px;
    font-family: "Montserrat", sans-serif;
    color: var(--white);
  }
  .contact__name {
    font-family: "Playfair Display", serif;
    font-weight: 600;
    font-size: 30px;
    color: var(--gold-name);
    line-height: 1.1;
  }
  .contact__role { font-size: 17px; margin-top: 4px; }
  .contact__service { font-size: 17px; line-height: 21px; margin-top: 22px; }
  .contact__list { list-style: none; margin-top: 20px; }
  .contact__item {
    display: flex; align-items: center; gap: 10px;
    font-size: 18px; height: 29px;
  }
  .contact__icon { width: 19px; height: 19px; flex: none; }
  .contact__note { font-size: 18px; color: var(--tag-yellow); margin-top: 14px; }

  .card--back .brand { left: 0; right: 0; top: 112px; }
  .card--back .brand__name { font-size: 72px; line-height: 88px; }
  .card--back .brand__tagline { font-size: 31px; line-height: 38px; color: var(--tag-yellow-bright); margin-top: 14px; }
</style>
</head>
<body>

<section class="card card--front">
  <svg class="front-art" width="774" height="473" viewBox="0 0 774 473">
    <defs>
      <linearGradient id="photoTones" x1="0" y1="0" x2="0" y2="1">
        <stop offset="0" stop-color="var(--photo-light)"/>
        <stop offset="1" stop-color="var(--photo-dark)"/>
      </linearGradient>
    </defs>
    <polygon class="front-art__stripe" points="455,0 470,0 355,473 340,473" fill="var(--olive-stripe)"/>
    <polygon class="front-art__photo" role="img" aria-label="Photo of a white two-storey home with dark exterior screen shades on the porch, garden and lawn chairs" points="470,0 774,0 774,473 355,473" fill="url(#photoTones)"/>
  </svg>

  <div class="brand">
    <p class="brand__name">Gilded<br>Slatworks</p>
    <p class="brand__tagline">Shutters Shades Blinds</p>
  </div>

  <div class="contact">
    <h1 class="contact__name">Daniel Trevick</h1>
    <p class="contact__role">Owner</p>
    <p class="contact__service">Custom Interior &amp; Exterior<br>Window Treatments</p>
    <ul class="contact__list">
      <li class="contact__item">
        <svg class="contact__icon" viewBox="0 0 20 20" aria-hidden="true">
          <path d="M2 7 Q10 1 18 7 L16 9 L13 7.5 L13 6 Q10 5 7 6 L7 7.5 L4 9 Z" fill="var(--white)"/>
          <rect x="4" y="10" width="12" height="7" rx="1" fill="var(--white)"/>
        </svg>
        <span>919-555-0148</span>
      </li>
      <li class="contact__item">
        <svg class="contact__icon" viewBox="0 0 20 20" aria-hidden="true">
          <circle cx="10" cy="10" r="8" fill="var(--white)"/>
          <path d="M6 5 Q9 7 8 10 Q6 12 7 15 M13 4 Q11 7 14 9 Q16 11 14 14" stroke="var(--ink-black)" stroke-width="1.6" fill="none"/>
        </svg>
        <span>GildedSlatworks.com</span>
      </li>
    </ul>
    <p class="contact__note">By Appointment</p>
  </div>
</section>

<section class="card card--back">
  <div class="brand">
    <p class="brand__name">Gilded<br>Slatworks</p>
    <p class="brand__tagline">Shutters Shades Blinds</p>
  </div>
</section>

</body>
</html>
```